Irrigation Business needs their business cards modernised and revamped

I would like to keep my current logo, colours and revamp the format of the card.

I would like the card to be clean yet important.

Im not sure if you include texture but i would like the named logo to be indented into the card etc.

show me something alive and free something thats clinical to the point yet has a feel of achievement. i would like people to go nice card.

Target Market(s)

high end clients, corporate, sports field manger, the guys that make the decisions

Industry/Entity Type

Business

Contact Information for Business Card

nformation to be included

Dean Harlow (Director)
0487305526
dean@kolvat.biz
www.kestonfieldworks.com

instagram logo
google logo
facebook logo

Colors

Designer to choose colors to be used in the design.

Requirements
Nice to have
• indentations a really nice feel to the card good texture

```html
<!DOCTYPE html>
<html lang="en">
<head>
<meta charset="UTF-8">
<title>Keston Fieldworks – Business Card</title>
<link rel="stylesheet" href="https://fonts.googleapis.com/css2?family=Montserrat:wght@400;600;700&family=Open+Sans:wght@400;600&display=swap">
<style>
  :root {
    --stage: #3a3a3a;
    --card-dark: #1c1c1d;
    --card-mid: #2a2a2b;
    --brand-blue: #2f6db5;
    --sky-blue: #2aa3db;
    --field-green: #1fa64a;
    --text-light: #f2f2f2;
    --icon-blue: #2f6db5;
    --band-dark: #111111;
  }
  * { box-sizing: border-box; margin: 0; padding: 0; }
  html, body { width: 1200px; height: 900px; overflow: hidden; }
  body {
    background: var(--stage);
    font-family: "Open Sans", Arial, sans-serif;
    position: relative;
  }
  .card {
    position: absolute;
    left: 250px;
    width: 700px;
    height: 400px;
    border-radius: 22px;
    overflow: hidden;
    background: radial-gradient(ellipse at 60% 40%, var(--card-mid), var(--card-dark) 75%);
    box-shadow: 0 10px 30px rgba(0,0,0,0.45);
  }
  .card--back { top: 40px; }
  .card--front { top: 470px; }

  .brand {
    display: flex;
    align-items: center;
    gap: 14px;
  }
  .brand__mark {
    border-radius: 50%;
    background: var(--sky-blue);
    flex: none;
  }
  .brand__name {
    font-family: "Montserrat", Arial, sans-serif;
    font-weight: 700;
    color: var(--brand-blue);
    text-transform: uppercase;
    letter-spacing: 0.5px;
    line-height: 1;
  }

  .card--back .brand {
    position: absolute;
    left: 0; right: 0; top: 140px;
    justify-content: center;
  }
  .card--back .brand__mark { width: 78px; height: 78px; }
  .card--back .brand__name { font-size: 34px; }
  .back__web {
    position: absolute;
    left: 0; right: 0; top: 262px;
    text-align: center;
    color: var(--text-light);
    font-size: 17px;
    letter-spacing: 0.3px;
  }

  .card--front .brand {
    position: absolute;
    left: 50px; top: 44px;
  }
  .card--front .brand__mark { width: 58px; height: 58px; }
  .card--front .brand__name { font-size: 25px; }

  .holder {
    position: absolute;
    right: 70px; top: 126px;
    text-align: right;
  }
  .holder__name {
    font-family: "Montserrat", Arial, sans-serif;
    font-weight: 600;
    font-size: 28px;
    line-height: 36px;
    color: var(--brand-blue);
    text-transform: uppercase;
    letter-spacing: 0.5px;
  }
  .holder__role {
    font-size: 19px;
    line-height: 26px;
    color: var(--text-light);
  }

  .front__rule {
    position: absolute;
    left: 50px; right: 60px; top: 200px;
    height: 1.5px;
    background: var(--field-green);
  }

  .contacts {
    position: absolute;
    left: 50px; top: 212px;
    list-style: none;
  }
  .contacts__item {
    display: flex;
    align-items: center;
    gap: 12px;
    color: var(--text-light);
    font-size: 17px;
    line-height: 27px;
  }
  .contacts__icon { width: 15px; height: 15px; flex: none; }

  .wave {
    position: absolute;
    left: 0; bottom: 0;
    width: 700px; height: 120px;
  }
  .social {
    position: absolute;
    right: 48px; bottom: 6px;
    display: flex;
    gap: 12px;
  }
  .social__dot {
    width: 28px; height: 28px;
    border-radius: 50%;
    background: var(--text-light);
  }
</style>
</head>
<body>

  <section class="card card--back" aria-label="Card back">
    <div class="brand">
      <span class="brand__mark"></span>
      <span class="brand__name">Keston Fieldworks</span>
    </div>
    <p class="back__web">www.kestonfieldworks.com</p>
  </section>

  <section class="card card--front" aria-label="Card front">
    <div class="brand">
      <span class="brand__mark"></span>
      <span class="brand__name">Keston Fieldworks</span>
    </div>

    <div class="holder">
      <p class="holder__name">Dean Harlow</p>
      <p class="holder__role">Director</p>
    </div>

    <div class="front__rule"></div>

    <ul class="contacts">
      <li class="contacts__item">
        <svg class="contacts__icon" viewBox="0 0 16 16"><path fill="var(--icon-blue)" d="M3.5 1.5l2.5 3-1.5 1.7c.9 1.9 2.3 3.3 4.3 4.3L10.5 9l3 2.5-1.4 2.7C6.5 13.8 2.2 9.5 1 3z"/></svg>
        <span>0487305526</span>
      </li>
      <li class="contacts__item">
        <svg class="contacts__icon" viewBox="0 0 16 16"><rect x="1" y="3" width="14" height="10" rx="1" fill="var(--icon-blue)"/><path d="M1.5 3.5L8 9l6.5-5.5" stroke="#1c1c1d" stroke-width="1.3" fill="none"/></svg>
        <span>dean@kolvat.biz</span>
      </li>
      <li class="contacts__item">
        <svg class="contacts__icon" viewBox="0 0 16 16"><circle cx="8" cy="8" r="6.5" fill="none" stroke="var(--icon-blue)" stroke-width="1.6"/><ellipse cx="8" cy="8" rx="2.8" ry="6.5" fill="none" stroke="var(--icon-blue)" stroke-width="1.2"/><path d="M1.5 8h13" stroke="var(--icon-blue)" stroke-width="1.2"/></svg>
        <span>kestonfieldworks.com</span>
      </li>
    </ul>

    <svg class="wave" viewBox="0 0 700 120" preserveAspectRatio="none" aria-hidden="true">
      <path d="M0 25 C160 78 320 62 470 60 C590 58 660 62 700 70 L700 120 L0 120 Z" fill="var(--sky-blue)"/>
      <path d="M0 34 C160 87 320 71 470 69 C590 67 660 71 700 78 L700 120 L0 120 Z" fill="var(--band-dark)"/>
      <path d="M0 39 C160 92 320 76 470 74 C590 72 660 76 700 82 L700 120 L0 120 Z" fill="var(--sky-blue)"/>
      <path d="M0 47 C160 100 320 84 470 82 C590 80 660 84 700 90 L700 120 L0 120 Z" fill="var(--brand-blue)"/>
    </svg>

    <div class="social" aria-label="Social channels">
      <span class="social__dot"></span>
      <span class="social__dot"></span>
      <span class="social__dot"></span>
    </div>
  </section>

</body>
</html>
```